Need a clean & modern homepage for an education site + opportunity for longer term work

Thanks for viewing our project. We are excited about this new website and we hope that we might build a relationship with designers as we work on this project. I provided quite a few details and requirements to help you more quickly create a design that meets our needs.
Who we are:
We are a website that discusses the importance of college accreditation and provides a directory of college programs.
What we need:
A homepage that meets the below requirements and is inspired by the examples provided
Definition of accredited:
ac·cred·it·ed [uh-kred-i-tid] adj.
1. officially recognized as meeting the essential requirements, as of academic excellence: accredited schools.
2. provided with official credentials, as by a government: an accredited diplomatic representative.
3. accepted as authoritative: an accredited theory.
Overall look and feel for the homepage:
- Clean, simple and modern
- Limited (or zero) pictures
- Utilize color blocks with text
- A trend seems to be longer vertical length homepages with lots of whitespace. I generally like this trend as long as the page is not way to tall.
Inspirations: Sites that have a similar look and feel to what I need.
http://lernvoxa.org/
http://www.campusmetrik.com/colleges/brantmoor-university/
http://quietfolding.org/
http://www.velostrahiring.com/
http://www.zunq.com/
http://sketches.bxv.com/
Items to be included on the homepage. Details below on each item.
- Top navigation
- Logo: Please leave a blank area for a logo. The logo has not been designed.
- Simple graphic/color block at the top that highlights a definition of “Accredited” – the definition should be formatted like it is being copy/pasted from a dictionary.
- Space for a video and small (50 word) written description of the video. You can use placeholder text.
- One section with 3 Paragraphs of content (each paragraph around 100 words) with a header at the top. You can use placeholder text but please create the formatting. At the end of the 3 paragraphs please have a “Read More” Note this shouldn't be 3 separate paragraphs with three read mores - it is 3 paragraphs with one read more at the end.
- An area with the header “Search Colleges by State” that has anchor text links to all 50 states.
Top navigation:
- Home
- States – with a subnav dropdown that includes all 50 US states.
- Programs – with a subnav dropdown that includes program titles (list below)
- Degrees - with a subnav dropdown that includes 5 degree levels (list below)
- Accreditation – no subnav
- Rankings – no subnav
- Resources – no subnav
Footer
- Link to about us, privacy, and a copyright www.url.com
Programs List for sub navigation
Accounting
Art
Bible
Business
Criminal Justice
Design
Education
Engineering
English
Law
LPN to RN
Management
Math
MBA
MPH
Medical Assisting
Military
Nursing
Occupational Therapy
Paralegal
Psychology
Pharmacy
RN to BSN
Radiology
Social Work
Sonography
Degrees list for sub navigation
Certificate
Associate
Bachelors
Masters
PhD
Thanks so much - looking forward to working with you!
Education

```html
<!DOCTYPE html>
<html lang="en">
<head>
<meta charset="utf-8">
<title>Accredora – College Accreditation</title>
<link href="https://fonts.googleapis.com/css2?family=Montserrat:ital,wght@0,400;0,500;0,600;0,700;0,800;1,400;1,500&family=Mulish:wght@400;600&display=swap" rel="stylesheet">
<style>
  :root {
    --red: #e06052;
    --charcoal: #454545;
    --paper: #fafafa;
    --menu: #666666;
    --ink: #3d3d3d;
    --muted: #555555;
    --sky: #a9c9dc;
    --mist: #d1dfe7;
    --teal: #2bbcc4;
    --white: #ffffff;
  }
  * { margin: 0; padding: 0; box-sizing: border-box; }
  html, body { width: 1200px; height: 2261px; overflow: hidden; }
  body {
    position: relative;
    background: var(--paper);
    font-family: "Mulish", Arial, sans-serif;
    color: var(--ink);
  }
  .abs { position: absolute; }
  a { color: inherit; text-decoration: none; }

  /* Header */
  .site-header { position: absolute; left: 0; top: 0; width: 1200px; height: 148px; background: var(--paper); z-index: 3; }
  .logo {
    position: absolute; left: 140px; top: 38px;
    font-family: "Montserrat", sans-serif; font-weight: 800;
    font-size: 40px; line-height: 37px; color: var(--red); letter-spacing: 0.5px;
  }
  .main-nav { position: absolute; top: 93px; left: 0; font-family: "Montserrat", sans-serif; font-weight: 500; font-size: 16px; color: var(--ink); }
  .main-nav a { position: absolute; white-space: nowrap; }
  .main-nav .caret { font-size: 9px; vertical-align: 3px; margin-left: 2px; }
  .nav-active {
    position: absolute; left: 470px; top: 84px; width: 127px; height: 38px;
    background: var(--menu); box-shadow: 0 2px 8px rgba(0,0,0,0.35);
  }
  .nav-active + a, .main-nav .on { color: var(--white); }

  /* Hero */
  .hero { position: absolute; left: 0; top: 148px; width: 1200px; height: 277px; z-index: 1; }
  .hero-word { position: absolute; left: 169px; top: 186px; font-family: "Montserrat", sans-serif; font-size: 24px; color: #e4e4e4; z-index: 2; }
  .hero-term { position: absolute; left: 168px; top: 225px; font-family: "Montserrat", sans-serif; font-size: 40px; font-weight: 500; color: var(--white); z-index: 2; }
  .hero-sound { position: absolute; left: 168px; top: 268px; font-family: "Montserrat", sans-serif; font-style: italic; font-size: 30px; color: var(--sky); z-index: 2; }
  .hero-pos { position: absolute; left: 169px; top: 310px; font-family: "Montserrat", sans-serif; font-style: italic; font-size: 20px; color: #8a8a8a; z-index: 2; }
  .hero-def { position: absolute; left: 620px; top: 182px; width: 420px; font-size: 15px; line-height: 33px; color: #dddddd; z-index: 2; }
  .hero-def p { margin-bottom: 33px; }

  /* Programs dropdown */
  .dropdown {
    position: absolute; left: 470px; top: 120px; width: 450px; height: 254px;
    background: var(--menu); border: 1px solid #888; box-shadow: 0 3px 10px rgba(0,0,0,0.45); z-index: 4;
    font-family: "Montserrat", sans-serif; font-weight: 600; font-size: 10.5px; color: var(--white); text-transform: uppercase;
  }
  .dropdown ul { position: absolute; top: 20px; list-style: none; }
  .dropdown li { height: 22.3px; }

  /* Video intro */
  .intro-text { position: absolute; left: 139px; top: 533px; width: 330px; font-size: 15.5px; line-height: 27.4px; color: var(--ink); }
  .video { position: absolute; left: 546px; top: 490px; width: 515px; height: 342px; background: var(--charcoal); border-radius: 7px; }
  .video-frame { position: absolute; left: 6px; top: 7px; width: 503px; height: 281px; background: linear-gradient(135deg, #6b5a4a, #4e443b 55%, #3f3833); }
  .play-btn { position: absolute; left: 238px; top: 123px; width: 40px; height: 38px; background: var(--white); }
  .progress-track { position: absolute; left: 13px; top: 313px; width: 421px; height: 8px; background: #5e5e5e; }
  .progress-fill { position: absolute; left: 0; top: 0; width: 127px; height: 8px; background: var(--teal); }
  .progress-knob { position: absolute; left: 123px; top: -4px; width: 9px; height: 16px; background: var(--white); }

  /* Paragraphs band */
  .band { position: absolute; left: 0; top: 860px; z-index: 0; }
  .para { position: absolute; top: 977px; width: 306px; text-align: center; color: var(--white); }
  .para h2 { font-family: "Montserrat", sans-serif; font-weight: 600; font-size: 25px; line-height: 33px; }
  .para p { margin-top: 26px; font-size: 15px; line-height: 22.2px; }
  .read-tab { position: absolute; left: 497px; top: 1296px; width: 207px; height: 42px; background: var(--red); }
  .read-more {
    position: absolute; left: 515px; top: 1280px; width: 171px; height: 44px; background: var(--white);
    font-family: "Montserrat", sans-serif; font-weight: 700; font-size: 15.5px; letter-spacing: 1.5px;
    color: var(--red); text-align: center; line-height: 44px;
  }

  /* States */
  .map-area { position: absolute; left: 113px; top: 1462px; width: 975px; height: 618px; background: var(--mist); border-radius: 120px 180px 260px 200px / 90px 120px 260px 220px; }
  .states-title {
    position: absolute; left: 0; top: 1455px; width: 1200px; text-align: center;
    font-family: "Montserrat", sans-serif; font-weight: 500; font-size: 42px; letter-spacing: 3px; color: var(--ink);
  }
  .state-col { position: absolute; top: 1584px; list-style: none; font-size: 16px; color: var(--muted); }
  .state-col li { height: 33.2px; }

  /* Footer */
  .footer-shape { position: absolute; left: 0; top: 2113px; }
  .footer-copy { position: absolute; left: 0; top: 2173px; width: 1200px; text-align: center; font-family: "Montserrat", sans-serif; font-size: 13px; color: var(--white); }
  .footer-links { position: absolute; left: 0; top: 2207px; width: 1200px; text-align: center; font-family: "Montserrat", sans-serif; font-size: 12px; color: var(--white); }
  .footer-links a { margin: 0 7px; }
</style>
</head>
<body>

<header class="site-header">
  <div class="logo">LOGO<br>HERE</div>
  <div class="nav-active"></div>
  <nav class="main-nav">
    <a style="left:324px">HOME</a>
    <a style="left:398px">STATES<span class="caret">▼</span></a>
    <a class="on" style="left:482px">PROGRAMS<span class="caret">▲</span></a>
    <a style="left:598px">DEGREES<span class="caret">▼</span></a>
    <a style="left:698px">ACCREDITATION</a>
    <a style="left:853px">RANKINGS</a>
    <a style="left:962px">RESOURCES</a>
  </nav>
</header>

<svg class="hero" width="1200" height="277" viewBox="0 0 1200 277" aria-hidden="true">
  <polygon points="0,0 1200,0 1200,229 600,277 0,229" fill="#454545"/>
</svg>
<div class="hero-word">“ACCREDITED”</div>
<div class="hero-term">ac·cred·it·ed</div>
<div class="hero-sound">[uh-kred-i-tid]</div>
<div class="hero-pos">adjective</div>
<div class="hero-def">
  <p>1. officially recognized as meeting the essential requirements, as of</p>
  <p>2. provided with official credentials: an accredited</p>
</div>

<div class="dropdown">
  <ul style="left:24px">
    <li>Accounting</li><li>Art</li><li>Bible</li><li>Business</li><li>Criminal Justice</li><li>Design</li><li>Education</li><li>Engineering</li><li>English</li><li>Law</li>
  </ul>
  <ul style="left:172px">
    <li>LPN to RN</li><li>Management</li><li>Math</li><li>MBA</li><li>MPH</li><li>Medical Assisting</li><li>Military</li><li>Nursing</li><li>Occupational Therapy</li><li>Paralegal</li>
  </ul>
  <ul style="left:329px">
    <li>Psychology</li><li>Pharmacy</li><li>RN to BSN</li><li>Radiology</li><li>Social Work</li><li>Sonography</li>
  </ul>
</div>

<p class="intro-text">Quam praesent. Ullamcorper dolor primis natoque dolor. Erat mollis. Aliquam facilisis. Vestibulum pharetra natoque pulvinar nec. Praesent risus, morbi lobortis odio pretium aptent. Hendrerit ligula varius iaculis nonummy enim. Pulvinar mauris quam eleifend, iaculis vestibulum cras, dui nullam vulputate eu Ridiculus sit platea quis mi. Cubilia netus purus nunc etiam.</p>

<div class="video">
  <div class="video-frame" role="img" aria-label="Video still: study desk from above with keyboard, notebooks, pencils and a phone">
    <svg class="play-btn" viewBox="0 0 40 38" aria-hidden="true"><rect width="40" height="38" fill="#fff"/><polygon points="14,10 28,19 14,28" fill="#444"/></svg>
  </div>
  <div class="progress-track"><div class="progress-fill"></div><div class="progress-knob"></div></div>
  <svg class="abs" style="left:453px;top:307px" width="22" height="20" viewBox="0 0 22 20" aria-hidden="true">
    <polygon points="2,7 6,7 11,2 11,18 6,13 2,13" fill="#fff"/>
    <path d="M14,6 Q17,10 14,14 M16,3 Q21,10 16,17" stroke="#fff" stroke-width="1.8" fill="none"/>
  </svg>
  <svg class="abs" style="left:485px;top:308px" width="18" height="18" viewBox="0 0 18 18" aria-hidden="true">
    <path d="M2,7 V2 H7 M11,2 H16 V7 M16,11 V16 H11 M7,16 H2 V11 M2,2 L7,7 M16,2 L11,7 M16,16 L11,11 M2,16 L7,11" stroke="#fff" stroke-width="2" fill="none"/>
  </svg>
</div>

<svg class="band" width="1200" height="620" viewBox="0 860 1200 620" aria-hidden="true">
  <path d="M0,864 Q600,946 1200,864 L1200,1470 Q600,1138 0,1470 Z" fill="#e06052"/>
</svg>

<div class="para" style="left:123px">
  <h2>PARAGRAPH<br>ONE</h2>
  <p>Facilisi curae justo facilisis porta pede vivamus sem urna eget. Condimentum ad vel feugiat ad aliquam ornare taciti Lorem Suspendisse Congue quisque nostra lacinia, pharetra lacinia rhoncus venenatis nullam id montes suspendisse vehicula blandit tortor pellentesque sociis.</p>
</div>
<div class="para" style="left:447px">
  <h2>PARAGRAPH<br>TWO</h2>
  <p>Nullam rutrum parturient viverra netus dictum felis purus lacinia amet Senectus ante Penatibus augue molestie eros pretium mauris. Faucibus condimentum convallis. Blandit porta lorem ante et gravida litora mus.</p>
</div>
<div class="para" style="left:770px">
  <h2>PARAGRAPH<br>THREE</h2>
  <p>Velit litora, interdum augue, dapibus vel ornare condimentum quis dis dolor rutrum malesuada. Dapibus aptent orci mi non nibh quisque donec. Vestibulum litora arcu varius mus dapibus nascetur. Nonummy hendrerit sociis ullamcorper interdum.</p>
</div>
<div class="read-tab"></div>
<a class="read-more">READ MORE</a>

<div class="map-area" role="img" aria-label="Map of the United States with state outlines"></div>
<h2 class="states-title">SEARCH COLLEGES BY STATE</h2>
<ul class="state-col" style="left:166px"><li>Alabama</li><li>Alaska</li><li>Arizona</li><li>Arkansas</li><li>California</li><li>Colorado</li><li>Connecticut</li><li>Delaware</li><li>Florida</li><li>Georgia</li></ul>
<ul class="state-col" style="left:360px"><li>Hawaii</li><li>Idaho</li><li>Illinois</li><li>Indiana</li><li>Iowa</li><li>Kansas</li><li>Kentucky</li><li>Louisiana</li><li>Maine</li><li>Maryland</li></ul>
<ul class="state-col" style="left:535px"><li>Massachusetts</li><li>Michigan</li><li>Minnesota</li><li>Mississippi</li><li>Missouri</li><li>Montana</li><li>Nebraska</li><li>Nevada</li><li>New Hampshire</li><li>New Jersey</li></ul>
<ul class="state-col" style="left:739px"><li>New Mexico</li><li>New York</li><li>North Carolina</li><li>North Dakota</li><li>Ohio</li><li>Oklahoma</li><li>Oregon</li><li>Pennsylvania</li><li>Rhode Island</li><li>South Carolina</li></ul>
<ul class="state-col" style="left:932px"><li>South Dakota</li><li>Tennessee</li><li>Texas</li><li>Utah</li><li>Vermont</li><li>Virginia</li><li>Washington</li><li>West Virginia</li><li>Wisconsin</li><li>Wyoming</li></ul>

<footer>
  <svg class="footer-shape" width="1200" height="148" viewBox="0 0 1200 148" aria-hidden="true">
    <polygon points="0,47 600,0 1200,47 1200,148 0,148" fill="#454545"/>
  </svg>
  <p class="footer-copy">COPYRIGHT © 2013 WWW.ACCREDORA.COM. ALL RIGHTS RESERVED.</p>
  <p class="footer-links"><a>ABOUT US</a><a>PRIVACY</a></p>
</footer>

</body>
</html>
```